Business Card Design

educational services
broker of essential services
So I love my The Velvet Kettle cards. I love the background.
I like the background on the copper valley card
I like a little part of each Meridel card
I want my card to stand out and be professional
I would also like somewhat of a brand
I do not want it to be specific to anything but the world and galaxy
I would like to be able to be used for everything, all encompassing
In spanish Cielo abierto, not sureother languages but i will do programs for other countries like China, Japan and Korea
Reason: It has been the first week of school and I have not been able to get the feedback I need.
Please change colors to Blue and GOld
Please add ~ over the n in Lorna
Please submit some vertical designs
Please include the world
Please make eagle a watermark
Make sure the Open Horizon doesnt have "preparatory school" under it
I am open to new designs and I will pay more after I chose a designer who seems to get all this stuff in my head!
Reason: Last minute designs were wonderful
Reason: I was out of town and not able to review the wonderful designs posted. I am narrowing the designs down now! I appreciate all the work done thus far.
Hello,
Thank you for all the designs. This is difficult. I have not been able to access them as I was able to last week so please be patient. If you also do web design please send me a message.
Again, thank you. I am down to just a few designs.
Sincerely,
Lorna Vickers Dunmore
I have been extremely busy, I should pick a design by the ned of this week. Thank you for your patience
Industry/Entity Type
Business
Contact Information for Business Card
Dr. Lorna Vickers Dunmore
www.ohacad.example
(555) 284-9306 US
lornajeanvickers@mailbox.example

```html
<!DOCTYPE html>
<html lang="en">
<head>
<meta charset="utf-8">
<title>Open Horizon – Business Card</title>
<link rel="stylesheet" href="https://fonts.googleapis.com/css2?family=Open+Sans:wght@400;700&display=swap">
<style>
  :root {
    --backdrop: #ebebeb;
    --paper: #ffffff;
    --burgundy: #6e0d32;
    --gold: #c2a810;
    --ink-light: #ffffff;
  }
  * { margin: 0; padding: 0; box-sizing: border-box; }
  html, body {
    width: 1200px; height: 977px; overflow: hidden;
    background: var(--backdrop);
    font-family: "Open Sans", Arial, sans-serif;
  }
  .card {
    position: absolute;
    left: 150px; top: 231px;
    width: 900px; height: 514px;
    background: var(--paper);
    overflow: hidden;
    box-shadow: 0 2px 10px rgba(0,0,0,0.12);
  }
  .card-bands { position: absolute; inset: 0; }
  .brand {
    position: absolute;
    right: 70px; top: 62px;
    display: flex; align-items: center; gap: 14px;
    color: var(--gold);
    font-weight: 700;
    font-size: 44px;
    letter-spacing: 1px;
    text-transform: uppercase;
  }
  .brand-dot {
    width: 34px; height: 34px; border-radius: 50%;
    background: var(--burgundy);
  }
  .contact {
    position: absolute;
    left: 440px; top: 228px;
    color: var(--ink-light);
  }
  .contact-name {
    font-weight: 700; font-size: 27px; margin-bottom: 12px;
  }
  .contact-line {
    display: flex; align-items: center; gap: 10px;
    font-size: 22px; line-height: 38px;
  }
  .contact-icon { width: 20px; height: 20px; flex: none; }
</style>
</head>
<body>
  <main class="card">
    <svg class="card-bands" viewBox="0 0 900 514" width="900" height="514" aria-hidden="true">
      <polygon points="0,318 900,138 900,514 0,514" fill="var(--burgundy)"/>
      <line x1="0" y1="318" x2="900" y2="138" stroke="var(--gold)" stroke-width="7"/>
    </svg>

    <div class="brand">
      <span class="brand-dot"></span>
      <span class="brand-name">Open Horizon</span>
    </div>

    <section class="contact">
      <p class="contact-name">Dr. Lorna Vickers Dunmore</p>
      <p class="contact-line">
        <svg class="contact-icon" viewBox="0 0 20 20"><circle cx="10" cy="10" r="10" fill="#fff"/><path d="M7 5.5l1.6 2.4-1 1.1c.7 1.4 1.6 2.3 3 3l1.1-1 2.4 1.6-.8 1.6c-3.8-.3-6.8-3.3-7.1-7.1z" fill="var(--burgundy)"/></svg>
        <span>(555) 284-9306 US</span>
      </p>
      <p class="contact-line">
        <svg class="contact-icon" viewBox="0 0 20 20"><circle cx="10" cy="10" r="10" fill="#fff"/><rect x="5" y="6.5" width="10" height="7" fill="none" stroke="var(--burgundy)" stroke-width="1.4"/><path d="M5 6.5l5 4 5-4" fill="none" stroke="var(--burgundy)" stroke-width="1.4"/></svg>
        <span>lornajeanvickers@mailbox.example</span>
      </p>
      <p class="contact-line">
        <svg class="contact-icon" viewBox="0 0 20 20"><circle cx="10" cy="10" r="10" fill="#fff"/><circle cx="10" cy="10" r="5.5" fill="none" stroke="var(--burgundy)" stroke-width="1.3"/><path d="M4.5 10h11M10 4.5c-2.5 3-2.5 8 0 11M10 4.5c2.5 3 2.5 8 0 11" fill="none" stroke="var(--burgundy)" stroke-width="1.1"/></svg>
        <span>www.ohacad.example</span>
      </p>
    </section>
  </main>
</body>
</html>
```